Kestrel Facilities Business Card Design

We would now like to design business cards with the new Kestrel Facilities logo

Target Market(s)

Professional

Industry/Entity Type

Professional services

Contact Information for Business Card

Employee name, title, phone number, email address, corporate office address and logo.

Font styles to use
Sans Serif

Colors
0054AA
0677BA
7BADD7
CADEEF
E8F1F8

Requirements
Must have
• My logo
Should not have
• any other pictures or images besides my logo

```html
<!DOCTYPE html>
<html lang="en">
<head>
<meta charset="utf-8">
<title>Kestrel Facilities Business Card</title>
<link rel="stylesheet" href="https://fonts.googleapis.com/css2?family=Montserrat:wght@400;500;700&display=swap">
<style>
  :root {
    --backdrop: #2b2b2b;
    --brand-blue: #3579c0;
    --brand-deep: #0054aa;
    --brand-mid: #0677ba;
    --brand-soft: #7badd7;
    --brand-pale: #e8f1f8;
    --silver: #d9dee6;
    --paper: #ffffff;
    --ink: #1c1c1c;
  }
  * { box-sizing: border-box; margin: 0; padding: 0; }
  html, body { width: 1200px; height: 1012px; overflow: hidden; }
  body {
    background: var(--backdrop);
    font-family: "Montserrat", sans-serif;
    position: relative;
  }
  .card {
    position: absolute;
    left: 250px;
    width: 700px;
    height: 400px;
    overflow: hidden;
  }
  .card--front { top: 66px; background: var(--brand-blue); }
  .card--back { top: 546px; background: var(--paper); }

  .brand {
    display: flex;
    align-items: center;
    gap: 14px;
    font-weight: 700;
    letter-spacing: 1px;
  }
  .brand__mark { display: block; flex: none; }
  .card--front .brand {
    position: absolute;
    left: 50%; top: 50%;
    transform: translate(-50%, -50%);
    color: var(--silver);
    font-size: 34px;
    white-space: nowrap;
  }
  .card--back .brand {
    position: absolute;
    left: 46px; top: 56px;
    color: var(--brand-deep);
    font-size: 26px;
    white-space: nowrap;
  }

  .backdrop-square {
    position: absolute;
    right: 56px; top: 40px;
    width: 290px; height: 290px;
    border: 34px solid var(--brand-pale);
  }

  .holder {
    position: absolute;
    right: 56px; top: 150px;
    text-align: right;
  }
  .holder__name {
    color: var(--brand-deep);
    font-weight: 700;
    font-size: 24px;
    letter-spacing: 0.5px;
  }
  .holder__title {
    color: var(--ink);
    font-size: 15px;
    margin-top: 4px;
  }
  .holder-tab {
    position: absolute;
    right: 0; top: 150px;
    width: 26px; height: 30px;
    background: var(--brand-deep);
  }

  .address {
    position: absolute;
    left: 46px; top: 170px;
    font-size: 16px;
    line-height: 1.45;
    color: var(--ink);
  }
  .contacts {
    position: absolute;
    left: 46px; top: 262px;
    list-style: none;
    font-size: 16px;
    color: var(--ink);
  }
  .contacts li {
    display: flex;
    align-items: center;
    gap: 10px;
    line-height: 26px;
  }
  .contacts svg { width: 16px; height: 16px; flex: none; }
</style>
</head>
<body>

<section class="card card--front" aria-label="Card front">
  <div class="brand">
    <svg class="brand__mark" width="30" height="30" viewBox="0 0 30 30" aria-hidden="true">
      <rect x="0" y="0" width="30" height="30" fill="var(--silver)"/>
    </svg>
    <span class="brand__name">KESTREL FACILITIES</span>
  </div>
</section>

<section class="card card--back" aria-label="Card back">
  <div class="backdrop-square" aria-hidden="true"></div>

  <div class="brand">
    <svg class="brand__mark" width="24" height="24" viewBox="0 0 24 24" aria-hidden="true">
      <rect x="0" y="0" width="24" height="24" fill="var(--brand-deep)"/>
    </svg>
    <span class="brand__name">KESTREL FACILITIES</span>
  </div>

  <p class="address">P.O Box 4410-00100<br>Nairobi, Kenya</p>

  <ul class="contacts">
    <li>
      <svg viewBox="0 0 16 16" aria-hidden="true"><path d="M3 1h3l1.5 4-2 1.3a9 9 0 0 0 4.2 4.2L11 8.5l4 1.5v3a2 2 0 0 1-2 2A12 12 0 0 1 1 3a2 2 0 0 1 2-2z" fill="var(--brand-deep)"/></svg>
      <span>+254-700-551-234</span>
    </li>
    <li>
      <svg viewBox="0 0 16 16" aria-hidden="true"><rect x="1" y="3" width="14" height="10" fill="var(--brand-deep)"/><path d="M1 3l7 6 7-6" stroke="#fff" stroke-width="1.4" fill="none"/></svg>
      <span>info@kestrelfacilities.com</span>
    </li>
    <li>
      <svg viewBox="0 0 16 16" aria-hidden="true"><circle cx="8" cy="8" r="7" fill="var(--brand-deep)"/><path d="M1 8h14M8 1c-3 4-3 10 0 14M8 1c3 4 3 10 0 14" stroke="#fff" stroke-width="1" fill="none"/></svg>
      <span>www.kestrelfacilities.com</span>
    </li>
  </ul>

  <div class="holder-tab" aria-hidden="true"></div>
  <div class="holder">
    <p class="holder__name">MUTHONI GRACE</p>
    <p class="holder__title">Co-Founder</p>
  </div>
</section>

</body>
</html>
```